Business card for my new company (Accounting firm)

I need a business card for my new business Brightwell Advisory and Ledger SA. Our services are accounting, tax, audit and financial management. Our customers are small companies, start-ups and new companies. The final design has to show financial security, trust and growth. Please find our logo attached to the business card. Text for the business card: Brightwell Advisory and Ledger SA Tomas Varenholt Director and Founder Certified Accountant Tel. 022 418 57 34 tv@clairevalconseil.ch www.clairevalconseil.ch Rue des Vergières 27 1201 Geneva
Target Market(s)
Our customers are small companies, start-ups and new companies.
Industry/Entity Type
Finance And Accounting
Contact Information for Business Card
Claireval Conseil et Comptes SA
Tomas Varenholt
Directeur et Fondateur
Expert-comptable diplômé
Tél. 022 418 57 34
tv@clairevalconseil.ch
www.clairevalconseil.ch
Rue des Vergières 27
1201 Genève

```html
<!DOCTYPE html>
<html lang="fr">
<head>
<meta charset="utf-8">
<title>Claireval Conseil et Comptes – Carte de visite</title>
<link rel="stylesheet" href="https://fonts.googleapis.com/css2?family=Montserrat:wght@500&family=Roboto:wght@400;700&display=swap">
<style>
  :root {
    --stage: #2b2b2d;
    --brand-blue: #1a6496;
    --accent-blue: #36ace0;
    --paper: #ffffff;
    --ink-dark: #3a3a3c;
    --ink-light: #ffffff;
  }
  * { box-sizing: border-box; margin: 0; padding: 0; }
  html, body {
    width: 1200px; height: 960px; overflow: hidden;
    background: var(--stage);
  }
  .canvas { position: relative; width: 1200px; height: 960px; }

  .card {
    position: absolute; width: 640px; height: 366px; overflow: hidden;
    box-shadow: 0 18px 40px rgba(0,0,0,.45);
  }
  .card--back { left: 90px; top: 90px; background: var(--brand-blue); }
  .card--front { left: 470px; top: 500px; background: var(--paper); }

  .card__wave { position: absolute; inset: 0; width: 100%; height: 100%; }

  .wordmark {
    position: absolute; text-align: center;
    font-family: "Montserrat", sans-serif; font-weight: 500;
  }
  .wordmark__name { display: block; font-size: 54px; letter-spacing: 4px; line-height: 1; }
  .wordmark__tagline { display: block; font-size: 14px; letter-spacing: 4.5px; margin-top: 8px; }

  .card--back .wordmark { left: 0; right: 0; top: 140px; color: var(--ink-light); }
  .card--front .wordmark { left: 0; right: 0; top: 70px; color: var(--ink-dark); }

  .holder {
    position: absolute; right: 250px; top: 262px; text-align: right;
    font-family: "Roboto", sans-serif; color: var(--ink-light);
  }
  .holder__name { font-size: 23px; font-weight: 700; line-height: 1.2; }
  .holder__role { font-size: 15px; font-weight: 400; line-height: 1.3; }

  .divider {
    position: absolute; left: 405px; top: 222px; width: 1px; height: 118px;
    background: rgba(255,255,255,.75);
  }

  .contact {
    position: absolute; left: 420px; top: 220px;
    font-family: "Roboto", sans-serif; color: var(--ink-light); font-size: 14px;
    list-style: none; line-height: 1.4;
  }
  .contact__address { margin-bottom: 10px; }
  .contact__item { display: flex; align-items: center; gap: 7px; }
  .contact__icon { width: 12px; height: 12px; flex: none; fill: var(--ink-light); }
</style>
</head>
<body>
<main class="canvas">

  <section class="card card--back" aria-label="Verso de la carte">
    <div class="wordmark">
      <span class="wordmark__name">CLAIREVAL</span>
      <span class="wordmark__tagline">CONSEIL ET COMPTES</span>
    </div>
  </section>

  <section class="card card--front" aria-label="Recto de la carte">
    <svg class="card__wave" viewBox="0 0 640 366" preserveAspectRatio="none" aria-hidden="true">
      <path d="M0,218 Q380,290 592,0 L640,0 L640,366 L0,366 Z" fill="var(--accent-blue)"/>
      <path d="M0,232 Q390,300 604,0 L640,0 L640,366 L0,366 Z" fill="var(--paper)"/>
      <path d="M0,236 Q394,304 608,0 L640,0 L640,366 L0,366 Z" fill="var(--brand-blue)"/>
    </svg>

    <div class="wordmark">
      <span class="wordmark__name">CLAIREVAL</span>
      <span class="wordmark__tagline">CONSEIL ET COMPTES</span>
    </div>

    <div class="holder">
      <p class="holder__name">Tomas Varenholt</p>
      <p class="holder__role">Directeur et Fondateur</p>
      <p class="holder__role">Expert-comptable diplômé</p>
    </div>

    <div class="divider"></div>

    <ul class="contact">
      <li class="contact__address">Rue des Vergières 27<br>1201 Genève</li>
      <li class="contact__item">
        <svg class="contact__icon" viewBox="0 0 24 24" aria-hidden="true"><path d="M6.6 10.8c1.4 2.8 3.8 5.1 6.6 6.6l2.2-2.2c.3-.3.7-.4 1-.2 1.1.4 2.3.6 3.6.6.6 0 1 .4 1 1V20c0 .6-.4 1-1 1C10.6 21 3 13.4 3 4c0-.6.4-1 1-1h3.5c.6 0 1 .4 1 1 0 1.3.2 2.5.6 3.6.1.3 0 .7-.2 1z"/></svg>
        <span>022 418 57 34</span>
      </li>
      <li class="contact__item">
        <svg class="contact__icon" viewBox="0 0 24 24" aria-hidden="true"><path d="M2 5h20v14H2z M2 5l10 8 10-8" fill="none" stroke="#fff" stroke-width="2"/></svg>
        <span>tv@clairevalconseil.ch</span>
      </li>
      <li class="contact__item">
        <svg class="contact__icon" viewBox="0 0 24 24" aria-hidden="true"><circle cx="12" cy="12" r="10" fill="none" stroke="#fff" stroke-width="2"/><path d="M2 12h20M12 2c3 3 3 17 0 20M12 2c-3 3-3 17 0 20" fill="none" stroke="#fff" stroke-width="1.6"/></svg>
        <span>www.clairevalconseil.ch</span>
      </li>
    </ul>
  </section>

</main>
</body>
</html>
```